Calvanto Group Real Estate Company business cards

New business card design, we are generally happy with the basic layout of the existing front of business card, (feel free to change) but require a head shot photo on the back side.

http://www.calvanto.com.au/

Attached logos, and existing business card

------------------------------

Target Market(s)

Real estate

Industry/Entity Type

Real Estate

Contact Information for Business Card

Standard size double sided

Font styles to use
Other font styles liked:
• Futura

Requirements
Must have
• Photo head shot on the back side
Nice to have
• yes
Should not have
• No

```html
<!DOCTYPE html>
<html lang="en">
<head>
<meta charset="utf-8">
<title>Calvanto Group Business Cards</title>
<link rel="stylesheet" href="https://fonts.googleapis.com/css2?family=Open+Sans:wght@400;600;700&family=Roboto+Condensed:wght@400&display=swap">
<style>
  :root {
    --stage: #000000;
    --purple: #312260;
    --navy: #22194a;
    --orange: #f18a1f;
    --card-light: #e9eaec;
    --card-light-2: #dcdde0;
    --white: #ffffff;
    --ink: #2a2440;
  }
  * { margin: 0; padding: 0; box-sizing: border-box; }
  html, body { width: 1200px; height: 900px; overflow: hidden; background: var(--stage); }
  body { position: relative; font-family: "Open Sans", Arial, sans-serif; }

  .card {
    position: absolute;
    top: 306px;
    height: 271px;
    border-radius: 10px;
    overflow: hidden;
  }
  .card-front { left: 149px; width: 439px; background: var(--purple); }
  .card-back {
    left: 608px; width: 441px;
    background: linear-gradient(90deg, var(--card-light) 0%, var(--card-light-2) 100%);
  }

  .brand { position: absolute; font-family: "Open Sans", Arial, sans-serif; font-weight: 400; white-space: nowrap; }
  .brand-name { display: block; line-height: 1; }
  .brand-group { display: block; text-align: right; text-transform: uppercase; line-height: 1; }

  .front-brand { left: 0; right: 0; top: 80px; color: var(--white); text-align: center; }
  .front-brand .brand-inner { display: inline-block; }
  .front-brand .brand-name { font-size: 72px; letter-spacing: 1px; }
  .front-brand .brand-group { font-size: 12px; letter-spacing: 6px; margin-top: -2px; margin-right: -6px; }

  .front-services {
    position: absolute; left: 0; right: 0; top: 173px;
    text-align: center;
    font-family: "Roboto Condensed", Arial, sans-serif;
    font-size: 22px;
    line-height: 1.2;
    color: var(--white);
  }
  .front-services .divider { margin: 0 14px; }

  .headshot {
    position: absolute; left: 0; top: 0; width: 207px; height: 271px;
    background: linear-gradient(180deg, #e4e5e7 0%, #c9c7c6 45%, #2c3346 100%);
  }

  .back-details { position: absolute; left: 225px; top: 0; right: 0; bottom: 0; color: var(--ink); }
  .back-brand { left: 0; top: 24px; color: var(--purple); }
  .back-brand .brand-name { font-size: 40px; }
  .back-brand .brand-group { font-size: 7px; letter-spacing: 3px; margin-top: 1px; margin-right: -3px; color: var(--ink); }

  .person-name { position: absolute; left: 0; top: 92px; font-size: 15px; font-weight: 600; color: var(--orange); }
  .person-role { position: absolute; left: 0; top: 113px; font-size: 12px; color: var(--ink); }
  .company-name { position: absolute; left: 1px; top: 137px; font-size: 14px; font-weight: 600; color: var(--orange); }
  .company-abn { position: absolute; left: 1px; top: 157px; font-size: 12px; color: var(--ink); }
  .company-abn strong { font-weight: 700; }

  .contact-list { position: absolute; left: 0; top: 191px; list-style: none; }
  .contact-list li {
    display: flex; align-items: center;
    height: 18.5px;
    font-size: 12px; color: var(--ink);
  }
  .contact-list svg { width: 9px; height: 9px; margin: 0 9px 0 3px; fill: var(--orange); flex: none; }
</style>
</head>
<body>
  <section class="card card-front" aria-label="Business card front">
    <div class="brand front-brand">
      <div class="brand-inner">
        <span class="brand-name">calvanto</span>
        <span class="brand-group">group</span>
      </div>
    </div>
    <div class="front-services">Buy<span class="divider">|</span>Sell<span class="divider">|</span>Rent</div>
  </section>

  <section class="card card-back" aria-label="Business card back">
    <div class="headshot" role="img" aria-label="Head shot photo of the director in a dark suit and blue tie"></div>
    <div class="back-details">
      <div class="brand back-brand">
        <span class="brand-name">calvanto</span>
        <span class="brand-group">group</span>
      </div>
      <div class="person-name">Daniel Tran</div>
      <div class="person-role">Director</div>
      <div class="company-name">Calvanto Group</div>
      <div class="company-abn"><strong>ABN:</strong> 51 624 083 917</div>
      <ul class="contact-list">
        <li>
          <svg viewBox="0 0 10 10" aria-hidden="true"><path d="M2 0.5 L3.6 0.5 L4.2 3 L3 3.8 C3.6 5.2 4.8 6.4 6.2 7 L7 5.8 L9.5 6.4 L9.5 8 C9.5 9 8.8 9.5 8 9.5 C4 9.2 0.8 6 0.5 2 C0.5 1.2 1 0.5 2 0.5 Z"/></svg>
          0412 568 304
        </li>
        <li>
          <svg viewBox="0 0 10 10" aria-hidden="true"><path d="M0.5 2 L9.5 2 L9.5 8.5 L0.5 8.5 Z M1.2 2.6 L5 5.5 L8.8 2.6" stroke="#e9eaec" stroke-width="0.8"/></svg>
          daniel.tran@calvanto.com.au
        </li>
        <li>
          <svg viewBox="0 0 10 10" aria-hidden="true"><circle cx="5" cy="5" r="4.5"/></svg>
          www.calvanto.com.au
        </li>
      </ul>
    </div>
  </section>
</body>
</html>
```